July 2022 Industrial Manufacturer Product Expo Mexico City

We manufacture large screws and fastners for large Mining equipment, Trains, large ships, airplanes, wind turbines, and so on. We also do custom work base on the customer needs. No matter the size we can make it.
We have a Expo coming up with companies all over the world. We have to stand out we are a family own business so our customer service will be above and beyond anyone can provide. We do not have a sales force to push our products and services we provide one on one service.
Plus@!! I'm looking for anything that you designers can come up with if it was your company to put on a business card, plus i want to do a 1 or 2 sided pamphlet, and then a website. We make Speciality Bolts for large mining equipment these bolts can be 3 to 4 foot long!!! Plus fasteners, Nuts, washers, any, size, strengths, special materials, we offer more of a ono on one customer service, We are a small company, family own, but can fulfill any type of orders. We can also provide special time lines for emergency orders. "We keep the machines running we here at KRV don't believe in down time" We want to hear any slogan based on our company to stand out.
Thanks i really appreciate all your work and options that we have to pick on. Plus just a thought we could possibly want to entertain a experience Marketing internet help maybe a employment possibility. Thanks

I need 2 cards one in Spanish and English Like the steel back ground maybe send me in some bright red and blue writing Same with the Black cards Please remove the word Military The logo KRV maybe integrate a picture of a Bolt 🔩 Thank you

Still looking for I need 2 cards one in Spanish and English Like the steel back ground maybe send me in some bright red and blue writing Same with the Black cards try bright writing Please remove the word Military The logo KRV maybe integrate a picture of a Bolt 🔩 Plus will need the company to make a brochure and website next Thank you

Target Market(s)

Large Mining, Ship, Train, Green Energy, VELM, and Government equipment. Throughout the World

Industry/Entity Type

We can Custom Manufacture any type of Fastners for Mining equipment, Trains, Ships, Green energy, Governments, or military projects. wind turbines,

Contact Information for Business Card

I attached the name and contact info that's on a card, plus the Company Logo. Would like industrial looking background with Bright Colors that will stand out!! If we can insert somewhere maybe on back that we "Custom Manufacture Any Size or Quantity Fastners for Large Mining Equipment, Trains, Ships, Green Energy Equipment or Government Projects

Font styles to use
Other font styles liked:
• You Pick, has to be bold, colorful standout, Professional looking Beable to read it.

Colors

Designer to choose colors to be used in the design.

Requirements
Must have
• Need in Spanish and English TO STANDOUT FROM THE REST OF THE EXPO!! See Business card details, Rounded corners
Nice to have
• Can i see some of the darker cards with Bright Red and Blue letters I like to see the different type of card material, heavy thickness, plastic, transparent, Metal types, Bright Colors, I saw like Raised letters like on the logo.

```html
<!DOCTYPE html>
<html lang="es">
<head>
<meta charset="utf-8">
<title>KRV – Tarjetas de presentación / Business cards</title>
<link href="https://fonts.googleapis.com/css2?family=Roboto+Condensed:wght@400;700&display=swap" rel="stylesheet">
<style>
  :root {
    --backdrop: #9c9c9c;
    --steel-light-1: #f7f7f6;
    --steel-light-2: #e3e4e6;
    --steel-dark-1: #2a2b2e;
    --steel-dark-2: #161618;
    --edge-blue: #1b8fd8;
    --brand-navy: #25318f;
    --brand-blue: #1f5fb8;
    --bright-blue: #2aa8ff;
    --bright-red: #e8232f;
    --steel: #5f5f63;
    --ink-grey: #555558;
    --silver: #d6d6d9;
  }
  * { box-sizing: border-box; margin: 0; padding: 0; }
  html, body { width: 1200px; height: 1050px; overflow: hidden; }
  body {
    background: var(--backdrop);
    font-family: "Roboto Condensed", "Arial Narrow", sans-serif;
    display: flex;
    flex-direction: column;
    align-items: center;
    justify-content: center;
    gap: 70px;
  }
  .card {
    width: 735px;
    height: 420px;
    border-radius: 14px;
    border-bottom: 6px solid var(--edge-blue);
    display: flex;
    flex-direction: column;
    align-items: center;
    justify-content: center;
    text-align: center;
    overflow: hidden;
  }
  .card--front {
    background:
      repeating-linear-gradient(90deg, rgba(255,255,255,0.25) 0 1px, rgba(0,0,0,0.015) 1px 3px),
      linear-gradient(135deg, var(--steel-light-1), var(--steel-light-2));
  }
  .card--back {
    background:
      repeating-linear-gradient(90deg, rgba(255,255,255,0.025) 0 1px, rgba(0,0,0,0.05) 1px 3px),
      linear-gradient(135deg, var(--steel-dark-1), var(--steel-dark-2));
  }

  .brand-name {
    font-weight: 700;
    font-size: 118px;
    line-height: 1;
    letter-spacing: 14px;
    padding-left: 14px;
    color: var(--steel);
  }
  .card--back .brand-name { color: var(--silver); }

  .tagline {
    margin-top: 10px;
    font-size: 26px;
    letter-spacing: 0.5px;
    color: var(--brand-navy);
  }
  .card--back .tagline { color: var(--bright-blue); font-weight: 700; }

  .holder {
    margin-top: 22px;
    font-weight: 700;
    font-size: 25px;
    color: var(--brand-blue);
  }
  .quotes {
    width: 600px;
    display: flex;
    align-items: center;
    gap: 10px;
    margin-top: 6px;
    font-size: 17px;
    font-weight: 700;
    color: var(--bright-red);
  }
  .quotes::before, .quotes::after {
    content: "";
    flex: 1;
    height: 1px;
    background: var(--ink-grey);
  }
  .contact-row {
    display: flex;
    gap: 18px;
    margin-top: 10px;
    font-size: 17px;
    color: var(--ink-grey);
  }
  .contact-item { display: flex; align-items: center; gap: 6px; }
  .contact-item svg { width: 15px; height: 15px; fill: var(--bright-red); }

  .bolt-motif {
    width: 300px;
    height: 14px;
    margin-top: 18px;
    border-radius: 7px;
    background: linear-gradient(180deg, #f2f2f4, #8d8e93 55%, #4a4b50);
  }
  .custom-line {
    width: 600px;
    margin-top: 18px;
    font-size: 17px;
    font-weight: 700;
    line-height: 1.35;
    letter-spacing: 0.3px;
    color: var(--bright-red);
  }
</style>
</head>
<body>
  <section class="card card--front" aria-label="Frente de la tarjeta (español)">
    <div class="brand-name">KRV</div>
    <p class="tagline">FABRICACION Y DISTRIBUCION DE TORNILLOS</p>
    <p class="holder">Lic. Marisol Ibarra Ortega</p>
    <p class="quotes">Cotizaciones en</p>
    <div class="contact-row">
      <span class="contact-item">
        <svg viewBox="0 0 24 24" aria-hidden="true"><path d="M6.6 10.8a15 15 0 0 0 6.6 6.6l2.2-2.2a1 1 0 0 1 1-.25 11.4 11.4 0 0 0 3.6.57 1 1 0 0 1 1 1V20a1 1 0 0 1-1 1A17 17 0 0 1 3 4a1 1 0 0 1 1-1h3.5a1 1 0 0 1 1 1c0 1.25.2 2.45.57 3.6a1 1 0 0 1-.25 1z"/></svg>
        5550142287
      </span>
      <span class="contact-item">
        <svg viewBox="0 0 24 24" aria-hidden="true"><path d="M7 2h10a2 2 0 0 1 2 2v16a2 2 0 0 1-2 2H7a2 2 0 0 1-2-2V4a2 2 0 0 1 2-2zm0 3v13h10V5z"/></svg>
        5550193364
      </span>
      <span class="contact-item">
        <svg viewBox="0 0 24 24" aria-hidden="true"><path d="M2 5h20v14H2zm2 2v.4l8 5 8-5V7l-8 5z"/></svg>
        ventas@krvtornillos.mx
      </span>
    </div>
  </section>

  <section class="card card--back" aria-label="Back of the card (English)" lang="en">
    <div class="brand-name">KRV</div>
    <p class="tagline">MANUFACTURE AND DISTRIBUTION OF BOLTS</p>
    <div class="bolt-motif" role="img" aria-label="Steel bolt motif"></div>
    <p class="custom-line">CUSTOM MANUFACTURE OF ANY SIZE OR QUANTITY OF FASTENERS FOR LARGE MINING EQUIPMENT, TRAINS, SHIPS, GREEN ENERGY EQUIPMENT OR GOVERNMENT PROJECTS</p>
  </section>
</body>
</html>
```